Private Investment Firm Needs PowerPoint Presentation Template

Design PowerPoint template, take Pinebrook-submitted rough presentation draft, and drop it into new template. See attached Project Brief file for more detail.
Updates

Some decent designs have been submitted but they seem to lack the understanding of our target markets. I am hopeful that more time and feedback will result in better results.

Target Market(s)

Private company owners and intermediaries.

Font styles to use
Serif

Colors
3176b5

Requirements
Must have
• See attached Project Brief.
Nice to have
Should not have
• No B2C fluff--this is a B2B project.

```html
<!DOCTYPE html>
<html lang="en">
<head>
<meta charset="utf-8">
<title>Pinebrook Capital – Overview</title>
<link href="https://fonts.googleapis.com/css2?family=Montserrat:wght@400;500;600&family=Libre+Baskerville:wght@400&display=swap" rel="stylesheet">
<style>
  :root {
    --brand-blue: #1570c4;
    --panel-blue: #0f6bc0;
    --photo-dark: #0b2f3a;
    --photo-mid: #15505c;
    --ink-gray: #4a4a4c;
    --white: #ffffff;
  }
  * { margin: 0; padding: 0; box-sizing: border-box; }
  html, body { width: 1200px; height: 676px; overflow: hidden; background: var(--white); }
  .slide {
    position: relative; width: 1200px; height: 676px; overflow: hidden;
    background: var(--white); font-family: "Montserrat", sans-serif;
  }
  .edge-bar-left { position: absolute; left: 0; top: 0; width: 44px; height: 676px; background: var(--brand-blue); }
  .edge-bar-right { position: absolute; right: 0; top: 0; width: 12px; height: 676px; background: var(--brand-blue); }
  .site-url {
    position: absolute; left: 21px; top: 336px;
    transform: translate(-50%, -50%) rotate(-90deg);
    font-family: "Libre Baskerville", serif; font-size: 14px; color: var(--white); white-space: nowrap;
  }
  .page-number {
    position: absolute; right: 40px; top: 18px;
    font-family: "Libre Baskerville", serif; font-size: 17px; color: #222;
  }
  .section-title {
    position: absolute; left: 86px; top: 82px;
    font-size: 28px; font-weight: 600; color: var(--brand-blue); letter-spacing: 0.5px;
  }
  .headline {
    position: absolute; right: 748px; top: 186px; text-align: right;
    font-size: 40px; font-weight: 500; line-height: 42px; color: var(--ink-gray);
  }
  .headline .accent { color: var(--brand-blue); }
  .photo-band {
    position: absolute; left: 483px; top: 101px; width: 705px; height: 470px;
    background: linear-gradient(120deg, var(--photo-dark) 0%, var(--photo-mid) 50%, var(--photo-dark) 100%);
  }
  .info-panel {
    position: absolute; left: 483px; top: 170px; width: 705px; height: 334px;
    background: var(--panel-blue); color: var(--white);
    padding: 54px 0 0 40px; font-size: 17.5px; line-height: 28px; font-weight: 400;
  }
  .info-list { list-style: none; }
  .info-list > li { position: relative; padding-left: 21px; margin-bottom: 28px; }
  .info-list li::before {
    content: ""; position: absolute; left: 1px; top: 9px; width: 8px; height: 8px;
    border: 2.5px solid var(--white); transform: rotate(45deg);
  }
  .sub-list { list-style: none; margin-top: 0; }
  .sub-list li { position: relative; padding-left: 22px; }
  .emphasis { font-weight: 600; text-decoration: underline; text-underline-offset: 3px; text-decoration-thickness: 1px; }
  .brand {
    position: absolute; left: 68px; top: 612px; display: flex; align-items: center; gap: 8px;
  }
  .brand-dot { width: 30px; height: 30px; border-radius: 50%; background: var(--brand-blue); }
  .brand-name { font-size: 17px; font-weight: 600; color: var(--brand-blue); letter-spacing: 1.5px; }
</style>
</head>
<body>
<div class="slide">
  <div class="edge-bar-left"></div>
  <div class="edge-bar-right"></div>
  <div class="site-url">www.pinebrookcapital.com</div>
  <div class="page-number">9</div>

  <h1 class="section-title">OVERVIEW</h1>

  <p class="headline">
    <span class="accent">We have</span><br>
    over 140<br>
    years of<br>
    combined<br>
    principal<br>
    investing<br>
    experience.
  </p>

  <div class="photo-band" role="img" aria-label="Photograph of scattered US dollar bills tinted dark teal"></div>

  <div class="info-panel">
    <ul class="info-list">
      <li>Offices in Boston and San Francisco with 12 investment profes-<br>sionals <span class="emphasis">fully dedicated</span> to Non-Control Capital investing</li>
      <li>Invest combinations of equity and subordinated debt securities</li>
      <li>Currently investing $260MM fourth fund
        <ul class="sub-list">
          <li>9 Fund IV investments made to date (as of November 1, 2018)</li>
          <li>Over $120MM of “dry powder” available for new investments</li>
        </ul>
      </li>
    </ul>
  </div>

  <div class="brand">
    <span class="brand-dot"></span>
    <span class="brand-name">PINEBROOK CAPITAL</span>
  </div>
</div>
</body>
</html>
```